Classy, Elegant, Simple Business Card Design

Looking to have a classy, simple, and elegant design. Want a top notch designed business card. I really like the look of the new torvane credit card. I also like the design I attached. I am trying to reach 21-29 year old females for booking us for there wedding or event. We offer Disc Jockey Service, Photo Booth Rentals, and Uplighting .

Target Market(s)

21-28 year old females

Contact Information for Business Card

Has to have logo, website, email, and phone number

Font styles to use
Other font styles liked:
• open to font choice, modern, clean
Designer to choose
33a6d7
0791cd
0555a3
ffffff

Requirements
Must have
• Has to have logo, website, email, and phone number
Nice to have
• I really like the design of the new torvane credit card. I also included my logo and some designs I like
Should not have
• clutter or too much info

```html
<!DOCTYPE html>
<html lang="en">
<head>
<meta charset="utf-8">
<title>Tidewell Events – Business Card</title>
<link rel="stylesheet" href="https://fonts.googleapis.com/css2?family=Poppins:wght@400;500;600&display=swap">
<style>
  :root {
    --page-bg: #1d1d1f;
    --front-top: #25567f;
    --front-bottom: #153c69;
    --accent: #1e9be0;
    --brand: #1a86d0;
    --white: #ffffff;
    --service-text: #555a60;
  }
  * { box-sizing: border-box; margin: 0; padding: 0; }
  html, body {
    width: 1200px; height: 1200px; overflow: hidden;
    background: var(--page-bg);
    font-family: "Poppins", sans-serif;
  }
  .card {
    position: absolute;
    left: 262px;
    width: 686px;
    height: 392px;
    overflow: hidden;
  }
  .card--front {
    top: 165px;
    background: linear-gradient(180deg, var(--front-top) 0%, var(--front-bottom) 100%);
  }
  .card--back {
    top: 653px;
    background: var(--white);
  }
  .person { position: absolute; left: 37px; top: 42px; }
  .person__name {
    color: var(--accent);
    font-size: 23px; font-weight: 500; line-height: 1.1;
    letter-spacing: 0.3px;
  }
  .person__title {
    color: var(--white);
    font-size: 15.5px; font-weight: 400; line-height: 1.3;
  }
  .contact { position: absolute; left: 37px; top: 104px; list-style: none; }
  .contact__item {
    display: flex; align-items: center; gap: 8px;
    color: var(--white);
    font-size: 16px; line-height: 20px;
  }
  .contact__icon { width: 14px; height: 14px; flex: none; }
  .front-brand {
    position: absolute; right: 36px; bottom: 40px;
    color: var(--brand);
    font-size: 84px; font-weight: 600; line-height: 1;
    letter-spacing: -1px;
  }
  .back-brand {
    position: absolute; left: 0; right: 0; top: 150px;
    display: flex; justify-content: center; align-items: center; gap: 14px;
    color: var(--brand);
    font-size: 44px; font-weight: 600; line-height: 1;
    letter-spacing: 1px;
  }
  .back-brand__dot {
    width: 16px; height: 16px; border-radius: 50%;
    background: var(--brand);
  }
  .services {
    position: absolute; left: 0; right: 0; top: 334px;
    text-align: center;
    color: var(--service-text);
    font-size: 16.5px; line-height: 1;
  }
  .services__sep { color: var(--accent); padding: 0 3px; }
</style>
</head>
<body>
  <section class="card card--front" aria-label="Business card front">
    <div class="person">
      <p class="person__name">Daniel Hart</p>
      <p class="person__title">President</p>
    </div>
    <ul class="contact">
      <li class="contact__item">
        <svg class="contact__icon" viewBox="0 0 24 24" aria-hidden="true"><path fill="#1e9be0" d="M6.6 10.8a15.1 15.1 0 0 0 6.6 6.6l2.2-2.2c.3-.3.7-.4 1-.2 1.1.4 2.3.6 3.6.6.6 0 1 .4 1 1V20c0 .6-.4 1-1 1A17 17 0 0 1 3 4c0-.6.4-1 1-1h3.5c.6 0 1 .4 1 1 0 1.3.2 2.5.6 3.6.1.3 0 .7-.2 1z"/></svg>
        555-214-7730
      </li>
      <li class="contact__item">
        <svg class="contact__icon" viewBox="0 0 24 24" aria-hidden="true"><rect x="2" y="5" width="20" height="14" rx="1" fill="#1e9be0"/><path d="M2 6l10 7 10-7" fill="none" stroke="#163f6c" stroke-width="1.6"/></svg>
        info@tidewellevents.com
      </li>
      <li class="contact__item">
        <svg class="contact__icon" viewBox="0 0 24 24" aria-hidden="true"><circle cx="12" cy="12" r="10" fill="#1e9be0"/><path d="M7 6c2 1 3 3 2 5s1 3 2 5M15 5c-1 2 0 3 2 4s2 3 1 5" fill="none" stroke="#163f6c" stroke-width="1.6"/></svg>
        www.tidewellevents.com
      </li>
    </ul>
    <p class="front-brand">Tidewell</p>
  </section>

  <section class="card card--back" aria-label="Business card back">
    <p class="back-brand"><span class="back-brand__dot"></span>Tidewell Events</p>
    <p class="services">Disc Jockey Service<span class="services__sep">•</span>Photo Booth Rentals<span class="services__sep">•</span>Uplighting .</p>
  </section>
</body>
</html>
```